Dorvik Electric Ltd

Looking for a single page website and Facebook page design. I am an electrical contractor based on Vancouver Island. I do service, custom homes, residential and commercial installations. My company just started out, so I don't have any pictures of installs yet. I have 25 years experience. I would like the colors to be my logo colors black and I have a black Brandt Halvard that will be my vehicle which I will have a wrap for.
Updates

I just posted the contest today, not sure why the deadline is the same day.

Industry/Entity Type

Electrician

Requirements
Must have
• Services provided, About me section, quote section,
Nice to have
• I am not quite sure yet, I need to see some designs first .

```html
<!DOCTYPE html>
<html lang="en">
<head>
<meta charset="utf-8">
<title>Dorvik Electric Ltd</title>
<link rel="stylesheet" href="https://fonts.googleapis.com/css2?family=Raleway:wght@400;500;600;700;800;900&display=swap">
<style>
:root{
  --black:#000;
  --band:#0b0b0b;
  --yellow:#f5ae0f;
  --blue:#1428d8;
  --white:#fff;
  --grey:#bdbdbd;
  --field:#111;
}
*{box-sizing:border-box;margin:0;padding:0}
html,body{width:1200px;height:4739px;overflow:hidden;background:var(--black)}
body{position:relative;font-family:"Raleway",sans-serif;color:var(--white)}
.abs{position:absolute}
.accent{color:var(--yellow)}
.section-title{position:absolute;left:0;width:1200px;text-align:center;font-weight:900;font-size:47px;letter-spacing:0.5px}
.btn{position:absolute;background:var(--blue);color:var(--white);border-radius:30px;font-weight:700;font-size:16px;display:flex;align-items:center;justify-content:center;letter-spacing:.3px}

/* header */
.brand{position:absolute;display:flex;flex-direction:column;align-items:center}
.brand-mark{border-radius:50%;border:4px solid var(--white)}
.brand-name{font-weight:700;color:var(--white);white-space:nowrap}
.call-pill{position:absolute;left:672px;top:-2px;width:386px;height:42px;background:var(--yellow);border-radius:0 0 80px 80px;display:flex;align-items:center;justify-content:center;gap:10px;color:#111;font-weight:800;font-size:19px}
.main-nav{position:absolute;top:86px;left:540px;width:540px;display:flex;justify-content:space-between;font-size:14px;font-weight:700}
.main-nav a{color:var(--white);text-decoration:none}

/* hero */
.hero{position:absolute;left:0;top:150px;width:1200px;height:710px}
.hero-title{position:absolute;left:0;width:1200px;text-align:center;font-weight:900;line-height:1;text-shadow:0 3px 8px rgba(0,0,0,.5)}

/* about */
.about-text{position:absolute;left:145px;top:1036px;width:428px;font-size:13.4px;line-height:24.6px;text-align:justify;color:#e8e8e8}

/* services */
.services-band{position:absolute;left:0;top:1478px;width:1200px;height:603px;background:var(--band)}
.service{position:absolute;width:316px;height:316px;border-radius:50%;border:2px solid var(--yellow);display:flex;flex-direction:column;align-items:center;text-align:center;padding-top:40px;background:var(--band)}
.service.is-active{background:var(--blue);border-color:var(--blue)}
.service h3{font-weight:700;font-size:22px;line-height:24px;margin-top:12px;height:50px;display:flex;align-items:center}
.service p{font-size:12.5px;line-height:22px;width:200px;margin-top:10px;color:#eee}
.service .chev{margin-top:8px}

/* gallery */
.gallery{position:absolute;left:142px;top:2296px;width:916px;display:grid;grid-template-columns:repeat(3,1fr);gap:6px}
.gallery .tile{height:274px;border:3px solid var(--yellow)}

/* news */
.news-card{position:absolute;top:3229px;width:436px;height:254px;border:2px solid var(--yellow);background:#000}
.news-img{position:absolute;left:12px;top:12px;width:190px;height:228px}
.date-badge{position:absolute;left:20px;top:20px;width:46px;height:50px;background:var(--yellow);color:#111;font-weight:800;font-size:13px;line-height:16px;display:flex;flex-direction:column;align-items:center;justify-content:center}
.news-body{position:absolute;left:228px;top:28px;width:196px}
.news-body h4{font-weight:700;font-size:21px;line-height:25px}
.news-body p{font-size:12.5px;line-height:23px;margin-top:10px;color:#e5e5e5}
.news-body .more{display:block;font-size:12px;font-weight:800;color:var(--yellow);margin-top:16px}
.slider-dots{position:absolute;top:3542px;left:560px;display:flex;gap:6px}
.slider-dots span{width:22px;height:3px;background:var(--white)}
.slider-dots span.on{background:var(--yellow)}

/* contact */
.contact-band{position:absolute;left:0;top:3640px;width:1200px;height:830px;background:var(--band)}
.contact-point{position:absolute;text-align:center;width:300px;font-size:13.5px;line-height:26px}
.contact-point strong{display:block;font-size:19px;line-height:26px;font-weight:700}
.field{position:absolute;height:40px;border:1.5px solid #cfcfcf;border-radius:22px;background:var(--field);font-size:12.5px;color:#ddd;padding:10px 28px}
.field.message{height:74px;border-radius:28px}

/* footer */
.footer-nav{position:absolute;top:4640px;left:516px;width:514px;display:flex;justify-content:space-between;font-size:14px;font-weight:700}
.social{position:absolute;width:46px;height:46px;border-radius:50%;border:2px solid var(--white)}
.social.is-active{background:var(--blue);border-color:var(--blue)}
.copyright{position:absolute;left:518px;top:4686px;font-size:11px;color:#ddd}
</style>
</head>
<body>

<!-- Header -->
<div class="brand" style="left:140px;top:18px;width:180px">
  <div class="brand-mark" style="width:84px;height:84px"></div>
  <div class="brand-name" style="font-size:14px;margin-top:8px">DORVIK ELECTRIC Ltd</div>
</div>
<div class="call-pill">
  <svg width="24" height="24" viewBox="0 0 24 24"><circle cx="12" cy="12" r="11" fill="#111"/><path d="M8 6.5c.6-.5 1.3-.4 1.7.2l1 1.6c.3.5.2 1.1-.2 1.5l-.7.6c.6 1.4 1.6 2.5 3 3.1l.6-.7c.4-.4 1-.5 1.5-.2l1.6 1c.6.4.7 1.1.2 1.7l-.8.9c-.6.6-1.5.8-2.3.5-3.1-1.2-5.4-3.5-6.6-6.6-.3-.8-.1-1.7.5-2.3z" fill="var(--yellow)"/></svg>
  Call : 044 -987-650-312
</div>
<nav class="main-nav">
  <a href="#home">HOME</a><a href="#about">ABOUT</a><a href="#services">SERVICES</a><a href="#gallery">GALLERY</a><a href="#news">NEWS</a><a href="#contact">CONTACT</a>
</nav>

<!-- Hero -->
<svg class="hero" viewBox="0 150 1200 710" aria-hidden="false">
  <defs>
    <linearGradient id="heroPhoto" x1="0" y1="0" x2="0" y2="1">
      <stop offset="0" stop-color="#7a7a7a"/>
      <stop offset=".55" stop-color="#5c5c5c"/>
      <stop offset=".75" stop-color="#3a3a3a"/>
      <stop offset="1" stop-color="#2a2a2a"/>
    </linearGradient>
  </defs>
  <ellipse cx="596" cy="496" rx="584" ry="340" fill="#ffffff"/>
  <ellipse cx="612" cy="506" rx="578" ry="342" fill="var(--yellow)"/>
  <ellipse cx="598" cy="500" rx="584" ry="340" fill="url(#heroPhoto)" role="img" aria-label="Greyscale photo of a waterfront city skyline under a cloudy sky"/>
</svg>
<div class="hero-title" style="top:424px;font-size:76px">DORVIK</div>
<div class="hero-title" style="top:506px;font-size:76px"><span class="accent">ELECTRIC</span> LTD</div>
<svg class="abs" style="left:574px;top:633px" width="52" height="52" viewBox="0 0 52 52"><circle cx="26" cy="26" r="23" fill="var(--white)"/><circle cx="26" cy="26" r="18" fill="var(--blue)"/><path d="M21 17l13 9-13 9z" fill="var(--white)"/></svg>

<!-- About -->
<h2 class="section-title" style="left:145px;width:auto;top:960px;text-align:left">ABOUT <span class="accent">US</span></h2>
<p class="about-text">Lorem ipsum dolor sit amet, consectetur adipiscing elit, sed do eiusmod tempor incididunt ut labore et dolore magna aliqua. Quis ipsum suspendisse ultrices gravida. Risus commodo viverra maecenas accumsan lacus vel facilisis. Lorem ipsum dolor sit amet, consectetur adipiscing elit, sed do eiusmod tempor incididunt ut labore et dolore magna aliqua. Quis ipsum suspendisse ultrices gravida. Risus commodo viverra maecenas accumsan lacus vel facilisis. Lorem ipsum dolor sit amet, consectetur adipiscing elit, sed do eiusmod tempor</p>
<div class="btn" style="left:145px;top:1288px;width:153px;height:58px">READ MORE</div>
<svg class="abs" style="left:620px;top:940px" width="450" height="500" viewBox="620 940 450 500">
  <defs>
    <linearGradient id="aboutPhoto" x1="0" y1="0" x2="1" y2="1">
      <stop offset="0" stop-color="#c98a3a"/>
      <stop offset=".5" stop-color="#6b5a3e"/>
      <stop offset="1" stop-color="#d9b23a"/>
    </linearGradient>
    <linearGradient id="truck" x1="0" y1="0" x2="0" y2="1">
      <stop offset="0" stop-color="#3a3a3a"/>
      <stop offset="1" stop-color="#111"/>
    </linearGradient>
  </defs>
  <path d="M850 948a212 212 0 0 1 212 212" fill="none" stroke="var(--yellow)" stroke-width="12"/>
  <path d="M850 948a212 212 0 0 0-212 212" fill="none" stroke="var(--white)" stroke-width="10"/>
  <circle cx="850" cy="1160" r="200" fill="url(#aboutPhoto)" role="img" aria-label="Electricians in hard hats working on a wiring panel"/>
  <rect x="608" y="1226" width="446" height="210" rx="60" fill="url(#truck)" role="img" aria-label="Black Brandt Halvard pickup truck with company wrap"/>
</svg>

<!-- Services -->
<div class="services-band"></div>
<h2 class="section-title" style="top:1566px">OUR <span class="accent">SERVICES</span></h2>
<div class="service" style="left:142px;top:1667px">
  <svg width="66" height="66" viewBox="0 0 66 66" fill="none" stroke="#fff" stroke-width="2.5"><path d="M6 30L33 8l27 22"/><path d="M13 25v34h40V25"/><rect x="22" y="36" width="22" height="18"/><path d="M33 36v18M22 45h22"/></svg>
  <h3>CUSTOM HOMES</h3>
  <p>Lorem ipsum dolor sit amet, consectetur adipiscing elit, sed do eiusmod tempor incididu</p>
  <svg class="chev" width="22" height="14" viewBox="0 0 22 14"><path d="M2 2l9 9 9-9" fill="none" stroke="var(--yellow)" stroke-width="3.5"/></svg>
</div>
<div class="service is-active" style="left:442px;top:1667px">
  <svg width="66" height="66" viewBox="0 0 66 66" fill="none" stroke="#fff" stroke-width="2.5"><path d="M8 28L33 8l25 20"/><path d="M14 24v34h38V24"/><rect x="20" y="32" width="10" height="8"/><rect x="36" y="32" width="10" height="8"/><rect x="28" y="44" width="10" height="14"/><path d="M6 58h54"/></svg>
  <h3>RESIDENTIAL<br>INSTALLATIONS</h3>
  <p>Lorem ipsum dolor sit amet, consectetur adipiscing elit, sed do eiusmod tempor incididu</p>
  <svg class="chev" width="22" height="14" viewBox="0 0 22 14"><path d="M2 2l9 9 9-9" fill="none" stroke="#fff" stroke-width="3.5"/></svg>
</div>
<div class="service" style="left:740px;top:1667px">
  <svg width="66" height="66" viewBox="0 0 66 66" fill="none" stroke="#fff" stroke-width="2.5"><rect x="12" y="20" width="22" height="40"/><rect x="34" y="8" width="20" height="52"/><path d="M18 28h4M26 28h4M18 36h4M26 36h4M18 44h4M26 44h4M40 16h4M48 16h2M40 24h4M48 24h2M40 32h4M48 32h2M40 40h4M48 40h2M6 60h54"/></svg>
  <h3>COMMERCIAL<br>INSTALLATIONS</h3>
  <p>Lorem ipsum dolor sit amet, consectetur adipiscing elit, sed do eiusmod tempor incididu</p>
  <svg class="chev" width="22" height="14" viewBox="0 0 22 14"><path d="M2 2l9 9 9-9" fill="none" stroke="var(--yellow)" stroke-width="3.5"/></svg>
</div>

<!-- Gallery -->
<h2 class="section-title" style="top:2190px">OUR <span class="accent">GALLERY</span></h2>
<div class="gallery">
  <div class="tile" role="img" aria-label="Hands installing a wall-mounted boiler" style="background:linear-gradient(135deg,#e9e9e9,#b9b9b9)"></div>
  <div class="tile" role="img" aria-label="Worker on a roof at sunset" style="background:linear-gradient(180deg,#d19a2a,#8a5a10)"></div>
  <div class="tile" role="img" aria-label="Blue two-storey house with garden path" style="background:linear-gradient(180deg,#8fa7c2,#4a5a6e 60%,#3d5a2a)"></div>
  <div class="tile" role="img" aria-label="Electrician on a ladder wiring a ceiling" style="background:linear-gradient(180deg,#cfcfcf,#8d8d8d)"></div>
  <div class="tile" role="img" aria-label="Technician servicing a heating unit" style="background:linear-gradient(135deg,#d8d8d8,#4a6aa0)"></div>
  <div class="tile" role="img" aria-label="Two workers in hi-vis beside an outdoor unit" style="background:linear-gradient(135deg,#c9ccd0,#e07a2a 60%,#b9c94a)"></div>
</div>
<svg class="abs" style="left:581px;top:2413px" width="38" height="38" viewBox="0 0 38 38"><circle cx="19" cy="19" r="18" fill="var(--blue)"/><path d="M19 12v14M12 19h14" stroke="#fff" stroke-width="3"/></svg>
<div class="btn" style="left:524px;top:2902px;width:153px;height:58px">LOAD MORE</div>

<!-- News -->
<h2 class="section-title" style="top:3118px">FROM THE <span class="accent">NEWS</span></h2>
<article class="news-card" style="left:147px">
  <div class="news-img" role="img" aria-label="Modern house with solar roof and lit garage" style="background:linear-gradient(180deg,#9fb4c8,#2b3a48 55%,#6a4a20)"></div>
  <div class="date-badge">AUG<span>2022</span></div>
  <div class="news-body">
    <h4>Nemo enim ipsam voluptatem</h4>
    <p>Lorem ipsum dolor sit amet, consectetur adipiscing elit, sed do eiusmod tempor incididunt ut labore et dolore</p>
    <span class="more">READ MORE</span>
  </div>
</article>
<article class="news-card" style="left:615px">
  <div class="news-img" role="img" aria-label="Rows of circuit breakers in a distribution panel" style="background:linear-gradient(135deg,#d9dde2,#5a6a8a 50%,#c9ced4)"></div>
  <div class="date-badge">AUG<span>2022</span></div>
  <div class="news-body">
    <h4>Nemo enim ipsam voluptatem</h4>
    <p>Lorem ipsum dolor sit amet, consectetur adipiscing elit, sed do eiusmod tempor incididunt ut labore et dolore</p>
    <span class="more">READ MORE</span>
  </div>
</article>
<div class="slider-dots"><span></span><span class="on"></span><span></span></div>

<!-- Contact -->
<div class="contact-band"></div>
<h2 class="section-title" style="top:3728px">CONTACT <span class="accent">US</span></h2>
<svg class="abs" style="left:0;top:3830px" width="1200" height="140" viewBox="0 3830 1200 140">
  <g stroke="#ccc" stroke-width="1.5" stroke-dasharray="2 3" fill="none">
    <path d="M330 3893H440"/><path d="M645 3893H770"/>
  </g>
  <path d="M440 3888l8 5-8 5z M770 3888l8 5-8 5z" fill="#fff"/>
  <!-- phone pin -->
  <path d="M276 3946l-12-8a52 52 0 1 1 24 0z" fill="var(--yellow)"/>
  <circle cx="276" cy="3892" r="44" fill="#fff"/>
  <path d="M263 3876c1.3-1 2.8-.9 3.6.4l2.4 3.6c.6 1 .4 2.3-.4 3.1l-1.6 1.4c1.4 3 3.6 5.4 6.6 6.8l1.4-1.6c.8-.8 2.1-1 3.1-.4l3.6 2.4c1.3.8 1.4 2.3.4 3.6l-1.8 2c-1.3 1.3-3.3 1.7-5 1.1-6.8-2.6-11.8-7.6-14.4-14.4-.6-1.7-.2-3.7 1.1-5z" fill="var(--blue)"/>
  <!-- home pin -->
  <path d="M589 3946l-12-8a52 52 0 1 1 24 0z" fill="var(--yellow)"/>
  <circle cx="589" cy="3892" r="46" fill="var(--blue)"/>
  <path d="M570 3894l19-16 19 16h-5v14h-10v-9h-8v9h-10v-14z" fill="#fff"/>
  <!-- mail pin -->
  <path d="M938 3946l-12-8a52 52 0 1 1 24 0z" fill="var(--yellow)"/>
  <circle cx="938" cy="3892" r="44" fill="#fff"/>
  <rect x="918" y="3878" width="40" height="28" rx="3" fill="var(--blue)"/>
  <path d="M920 3881l18 13 18-13" fill="none" stroke="#fff" stroke-width="2.5"/>
</svg>
<div class="contact-point" style="left:126px;top:3970px"><strong>Phone</strong><strong>044 -987-650-312</strong></div>
<div class="contact-point" style="left:439px;top:3976px">421,ed ut perspiciatis unde omnis<br>45452 iste natus erro</div>
<div class="contact-point" style="left:788px;top:3976px">Email<br>hello@dorvikelectric.ca</div>

<div class="field" style="left:219px;top:4092px;width:371px">Enter Name</div>
<div class="field" style="left:609px;top:4092px;width:372px">Enter Email</div>
<div class="field" style="left:219px;top:4152px;width:371px">Phone</div>
<div class="field" style="left:609px;top:4152px;width:372px">Address</div>
<div class="field message" style="left:219px;top:4212px;width:762px">Message</div>
<div class="btn" style="left:524px;top:4322px;width:153px;height:58px">SUBMIT</div>

<!-- Footer -->
<svg class="abs" style="left:0;top:4460px" width="1200" height="279" viewBox="0 4460 1200 279">
  <ellipse cx="590" cy="4880" rx="620" ry="414" fill="#fff"/>
  <ellipse cx="612" cy="4886" rx="610" ry="408" fill="var(--yellow)"/>
  <ellipse cx="600" cy="4890" rx="606" ry="414" fill="#000"/>
</svg>
<div class="brand" style="left:170px;top:4552px;width:250px">
  <div class="brand-mark" style="width:130px;height:130px"></div>
  <div class="brand-name" style="font-size:21px;margin-top:8px">DORVIK ELECTRIC Ltd</div>
</div>
<div class="social" style="left:518px;top:4568px"></div>
<div class="social" style="left:581px;top:4568px"></div>
<div class="social is-active" style="left:643px;top:4568px"></div>
<nav class="footer-nav"><span>HOME</span><span>ABOUT</span><span>SERVICES</span><span>GALLERY</span><span>NEWS</span><span>CONTACT</span></nav>
<p class="copyright">© 2022 Dorvik Electric Ltd. All rights reserved.Privacy &nbsp;| &nbsp;Terms of Use</p>

</body>
</html>
```